Drinks Menu for Entertainment Venue

Need a drinks menu that is easier for an older demographic who can't use QR codes.
These are all the costs and information we need on it.
I made this within an hour on canva but as we are a world class venue I need his revamped, more professional and beautifully presented.
Pink are the main colours.
No pictures needed.
3 fold is also not required if there is a better design.

Target Market(s)

45-60

Industry/Entity Type

Entertainment and Hospitality

Colors
E54698
E96AAD
F1A4CE
F9D9EA
FCEFF6

Requirements
Must have
• Colour, easy to ready

```html
<!DOCTYPE html>
<html lang="en">
<head>
<meta charset="utf-8">
<title>Velvet Lantern Lounge – Drinks Menu</title>
<link rel="stylesheet" href="https://fonts.googleapis.com/css2?family=Fredoka:wght@500;600;700&family=Poppins:wght@400;500;600&family=Kaushan+Script&display=swap">
<style>
:root{
  --rose:#E54698;
  --rose-mid:#E96AAD;
  --rose-soft:#F1A4CE;
  --blush:#F9D9EA;
  --mist:#FCEFF6;
  --panel:#F5B6D9;
  --tag:#E13FA0;
  --hot:#EE3EA8;
  --ink:#121012;
  --paper:#ffffff;
  --stage:#ebebec;
}
*{box-sizing:border-box;margin:0;padding:0}
html,body{width:674px;height:1200px;overflow:hidden;background:var(--stage)}
body{position:relative;font-family:"Poppins",sans-serif;color:var(--ink)}

.spread{position:absolute;left:27px;width:620px;height:480px;overflow:hidden;
  background:linear-gradient(180deg,var(--panel) 0%,#F3ACD3 100%);
  box-shadow:0 6px 18px rgba(0,0,0,.22)}
.spread--outside{top:100px}
.spread--inside{top:620px}

.waves{position:absolute;left:0;right:0;bottom:0;height:95px;
  background:linear-gradient(180deg,rgba(249,217,234,0) 0%,var(--blush) 45%,var(--rose-soft) 100%)}

.band{display:inline-block;background:var(--ink);color:#fff;
  font:600 10.5px/1 "Fredoka",sans-serif;letter-spacing:.6px;text-transform:uppercase;
  padding:3px 20px 3px 13px;
  clip-path:polygon(3% 8%,100% 0,96% 50%,100% 100%,2% 92%,0 50%)}

.row{display:flex;justify-content:space-between;align-items:center;
  font:500 6.3px/10.3px "Poppins",sans-serif;white-space:nowrap}
.price{background:var(--tag);color:#fff;border-radius:1.5px;padding:0 2px;
  font:600 5.6px/7.6px "Poppins",sans-serif;flex:none}
.price--dark{background:var(--ink)}

.section{position:absolute}
.section .list{margin-top:5px}

/* outside spread */
.wine-panel{position:absolute;left:17px;top:0;width:183px;height:100%}
.wine-panel .section{left:0;width:183px}
.wine-panel .band{margin-left:-3px}

.spirits-panel{position:absolute;left:221px;top:0;width:172px;height:430px;background:var(--paper);
  clip-path:polygon(0 0,100% 0,99% 8%,100% 20%,98.5% 35%,100% 50%,99% 66%,100% 82%,99% 100%,
  88% 99%,74% 100%,58% 98.8%,42% 100%,26% 99%,12% 100%,0 99%,1.2% 80%,0 62%,1% 44%,0 26%,1.3% 12%)}
.spirits-panel .band{position:absolute;left:14px;top:27px}
.spirits-panel .groups{position:absolute;left:20px;right:14px;top:48px}
.spirits-panel .group{margin-bottom:10px}

.hero-illustration{position:absolute;left:424px;top:168px;width:190px;height:190px;border-radius:50%;
  background:radial-gradient(circle at 60% 40%,#3a1a2e 0%,var(--ink) 60%)}
.hero-bird{position:absolute;left:470px;top:140px;width:100px;height:150px;border-radius:50% 50% 40% 40%;
  background:linear-gradient(180deg,var(--rose-mid),var(--rose) 70%,transparent 100%);opacity:.85}

.brand{position:absolute;left:408px;top:62px;width:210px;display:flex;align-items:center;justify-content:center;gap:7px}
.brand__dot{flex:none;width:14px;height:14px;border-radius:50%;background:var(--ink)}
.brand__name{font:600 17px/1.1 "Fredoka",sans-serif;color:var(--hot)}

.title{position:absolute;left:400px;width:220px;text-align:center}
.title__drinks{top:342px;font:700 46px/1 "Fredoka",sans-serif;color:var(--hot);letter-spacing:1px}
.title__menu{top:376px;font:400 34px/1 "Kaushan Script",cursive;color:var(--ink)}

.corner-bird{position:absolute;left:-6px;top:360px;width:176px;height:124px;
  background:radial-gradient(circle at 40% 70%,#fff 0 45%,rgba(255,255,255,0) 46%),
  linear-gradient(160deg,rgba(229,70,152,.0) 20%,rgba(229,70,152,.55) 60%,rgba(40,20,30,.35))}

/* inside spread */
.classics-panel{position:absolute;left:16px;top:0;width:172px;height:404px;background:var(--paper);
  clip-path:polygon(0 0,100% 0,99% 15%,100% 32%,98.8% 50%,100% 70%,99% 88%,100% 100%,
  84% 99%,66% 100%,48% 98.8%,30% 100%,14% 99%,0 100%,1% 85%,0 65%,1.3% 45%,0 25%)}
.classics-head{position:absolute;left:30px;top:20px;width:112px;text-align:center}
.classics-head__drinks{display:block;background:var(--hot);color:#fff;font:700 16px/1.15 "Fredoka",sans-serif;
  letter-spacing:.5px;clip-path:polygon(2% 10%,100% 0,97% 55%,100% 100%,0 92%,3% 50%)}
.classics-head__menu{display:block;margin-top:-4px;font:400 15px/1 "Kaushan Script",cursive;color:var(--ink)}

.drink{position:absolute;width:132px}
.drink__top{display:flex;justify-content:space-between;align-items:flex-start}
.drink__name{font:600 8.8px/1 "Fredoka",sans-serif;color:var(--hot);text-transform:uppercase;letter-spacing:.3px}
.drink__desc{margin-top:2px;font:400 4.4px/1.3 "Poppins",sans-serif;color:#3a2a33;width:82px}
.classics-panel .drink{left:24px}
.classics-bird{position:absolute;left:75px;top:395px;width:120px;height:85px;border-radius:50% 50% 0 0;
  background:linear-gradient(180deg,var(--rose-mid),var(--rose-soft))}

.cocktails{position:absolute;left:225px;top:0;width:172px;height:100%}
.cocktails .band{position:absolute;left:0;top:27px}
.cocktails .drink{left:0;width:172px}
.cocktails .drink__desc{width:110px}

.extras{position:absolute;left:432px;top:0;width:168px;height:100%}
.extras .section{left:0;width:168px}
.extras .row{font-size:6.1px;line-height:10px}

.tall-bird{position:absolute;left:452px;top:290px;width:150px;height:190px;border-radius:45% 45% 0 0;
  background:linear-gradient(180deg,var(--rose-mid) 0%,var(--rose) 45%,rgba(229,70,152,.2) 100%);opacity:.8}
</style>
</head>
<body>

<section class="spread spread--outside" aria-label="Menu outside spread">
  <div class="waves" role="img" aria-label="Layered pink wave pattern"></div>
  <div class="corner-bird" role="img" aria-label="Illustration of a flamingo taking flight over a white circle"></div>

  <div class="wine-panel">
    <div class="section" style="top:25px">
      <span class="band">White wine - bottle</span>
      <div class="list">
        <div class="row"><span>Hollow creek chardonnay</span><span class="price">$12.00</span></div>
        <div class="row"><span>Marsh lane valley pinot grigio</span><span class="price">$12.00</span></div>
        <div class="row"><span>Bell lane pinot gris</span><span class="price">$15.00</span></div>
        <div class="row"><span>Tidestone point sauvignon blanc</span><span class="price">$14.00</span></div>
      </div>
    </div>
    <div class="section" style="top:113px">
      <span class="band">Rose wine - bottle</span>
      <div class="list">
        <div class="row"><span>Misty cove pinot noir</span><span class="price">$12.00</span></div>
      </div>
    </div>
    <div class="section" style="top:164px">
      <span class="band">Red wine - bottle</span>
      <div class="list">
        <div class="row"><span>Misty cove pinot noir</span><span class="price">$12.00</span></div>
        <div class="row"><span>Stonegate ridge shiraz</span><span class="price">$12.00</span></div>
      </div>
    </div>
    <div class="section" style="top:233px">
      <span class="band">Champagne</span>
      <div class="list">
        <div class="row"><span>Maison aurel</span><span class="price">$12.00</span></div>
        <div class="row"><span>Delacour brut reserve nv</span><span class="price">$12.00</span></div>
        <div class="row"><span>Veuve marchal brut nv</span><span class="price">$12.00</span></div>
      </div>
    </div>
    <div class="section" style="top:309px">
      <span class="band">Sparkling wine</span>
      <div class="list">
        <div class="row"><span>Misty cove pinot noir</span><span class="price">$12.00</span></div>
        <div class="row"><span>Stonegate ridge shiraz</span><span class="price">$12.00</span></div>
      </div>
    </div>
  </div>

  <div class="spirits-panel">
    <span class="band">Spirits</span>
    <div class="groups">
      <div class="group">
        <div class="row"><span>Nordvik vanilla vodka</span><span class="price">$12.00</span></div>
        <div class="row"><span>Nordvik vodka</span><span class="price">$12.00</span></div>
        <div class="row"><span>Palisade vodka</span><span class="price">$15.00</span></div>
        <div class="row"><span>Verrine vodka</span><span class="price">$14.00</span></div>
      </div>
      <div class="group">
        <div class="row"><span>Amalva original gin</span><span class="price">$14.00</span></div>
        <div class="row"><span>Amalva rosa gin</span><span class="price">$14.00</span></div>
        <div class="row"><span>Meadowsong pink gin</span><span class="price">$15.00</span></div>
        <div class="row"><span>Meadowsong signature dry gin</span><span class="price">$15.00</span></div>
      </div>
      <div class="group">
        <div class="row"><span>Cumbre plata tequila</span><span class="price">$12.00</span></div>
        <div class="row"><span>Cumbre reposado tequila</span><span class="price">$15.00</span></div>
        <div class="row"><span>Don aurelio 1948</span><span class="price">$20.00</span></div>
      </div>
      <div class="group">
        <div class="row"><span>Hollis creek bourbon</span><span class="price">$12.00</span></div>
        <div class="row"><span>Delta velvet</span><span class="price">$12.00</span></div>
      </div>
      <div class="group">
        <div class="row"><span>Northern pine</span><span class="price">$12.00</span></div>
        <div class="row"><span>Kestrel reserve 12 yo</span><span class="price">$12.00</span></div>
        <div class="row"><span>Hickory hollow</span><span class="price">$14.00</span></div>
        <div class="row"><span>Glenmarr black</span><span class="price">$14.00</span></div>
        <div class="row"><span>Glenmarr blue</span><span class="price">$50.00</span></div>
      </div>
      <div class="group">
        <div class="row"><span>Bahia white rum</span><span class="price">$12.00</span></div>
        <div class="row"><span>Canefield rum</span><span class="price">$12.00</span></div>
        <div class="row"><span>Coco bay</span><span class="price">$11.00</span></div>
        <div class="row"><span>Old anchor spiced rum</span><span class="price">$12.00</span></div>
      </div>
      <div class="group">
        <div class="row"><span>Framboise royale</span><span class="price">$11.00</span></div>
        <div class="row"><span>Orangerie</span><span class="price">$11.00</span></div>
        <div class="row"><span>Casalino amaretto</span><span class="price">$12.00</span></div>
        <div class="row"><span>Krauterhof</span><span class="price">$11.00</span></div>
      </div>
      <div class="group">
        <div class="row"><span>Maison verlaine xo</span><span class="price">$35.00</span></div>
        <div class="row"><span>Maison verlaine vsop</span><span class="price">$16.00</span></div>
      </div>
    </div>
  </div>

  <div class="brand">
    <span class="brand__dot"></span>
    <p class="brand__name">Velvet Lantern Lounge</p>
  </div>
  <div class="hero-illustration" role="img" aria-label="Flamingo standing on one leg in front of a black circle"></div>
  <div class="hero-bird" role="img" aria-label="Pink flamingo body rising above the circle"></div>
  <p class="title title__drinks">DRINKS</p>
  <p class="title title__menu">Menu</p>
</section>

<section class="spread spread--inside" aria-label="Menu inside spread">
  <div class="waves" role="img" aria-label="Layered pink wave pattern"></div>
  <div class="tall-bird" role="img" aria-label="Illustration of a flamingo bending to sip a beer"></div>

  <div class="classics-panel">
    <div class="classics-head">
      <span class="classics-head__drinks">DRINKS</span>
      <span class="classics-head__menu">Menu</span>
    </div>
    <div class="drink" style="top:72px"><div class="drink__top"><span class="drink__name">Margarita</span><span class="price price--dark">$12.00</span></div><p class="drink__desc">Tart/Sweet/Tangy Tequila/ Triple sec/ Sweet and Sour Mix</p></div>
    <div class="drink" style="top:108px"><div class="drink__top"><span class="drink__name">Passionfruit<br>Margarita</span><span class="price price--dark">$12.00</span></div><p class="drink__desc">Tart/Sweet/Tangy Tequila/ Triple sec/ Sweet and Sour Mix</p></div>
    <div class="drink" style="top:153px"><div class="drink__top"><span class="drink__name">Chilli Margarita</span><span class="price price--dark">$12.00</span></div><p class="drink__desc">Tart/Sweet/Tangy Tequila/ Triple sec/ Sweet and Sour Mix</p></div>
    <div class="drink" style="top:192px"><div class="drink__top"><span class="drink__name">Mojito</span><span class="price price--dark">$12.00</span></div><p class="drink__desc">Tart/Sweet/Tangy Tequila/ Triple sec/ Sweet and Sour Mix</p></div>
    <div class="drink" style="top:232px"><div class="drink__top"><span class="drink__name">Pornstar Martini</span><span class="price price--dark">$12.00</span></div><p class="drink__desc">Tart/Sweet/Tangy Tequila/ Triple sec/ Sweet and Sour Mix</p></div>
    <div class="drink" style="top:269px"><div class="drink__top"><span class="drink__name">Espresso Martini</span><span class="price price--dark">$12.00</span></div><p class="drink__desc">Tart/Sweet/Tangy Tequila/ Triple sec/ Sweet and Sour Mix</p></div>
    <div class="drink" style="top:307px"><div class="drink__top"><span class="drink__name">Amaretto Sour</span><span class="price price--dark">$12.00</span></div><p class="drink__desc">Tart/Sweet/Tangy Tequila/ Triple sec/ Sweet and Sour Mix</p></div>
    <div class="drink" style="top:345px"><div class="drink__top"><span class="drink__name">Long Island<br>Iced Tea</span><span class="price price--dark">$12.00</span></div><p class="drink__desc">Tart/Sweet/Tangy Tequila/ Triple sec/ Sweet and Sour Mix</p></div>
  </div>
  <div class="classics-bird" role="img" aria-label="Illustration of a flamingo resting among the waves"></div>

  <div class="cocktails">
    <span class="band">Signature cocktails</span>
    <div class="drink" style="top:56px"><div class="drink__top"><span class="drink__name">Velvet Midnight<br>Tonic</span><span class="price">$30.00</span></div><p class="drink__desc">Sweet/Anise/Strong! A cure for everything! Miracle hair growth, marvellous vigour remedy, eternal youth wonder elixir and so much more!</p></div>
    <div class="drink" style="top:119px"><div class="drink__top"><span class="drink__name">Bubbles &amp; Ice Pop</span><span class="price">$20.00</span></div><p class="drink__desc">Bubbly/Fresh/Light Prosecco/Ice pop.</p></div>
    <div class="drink" style="top:149px"><div class="drink__top"><span class="drink__name">Petal Punch</span><span class="price">$24.00</span></div><p class="drink__desc">Tropical/Floral/Aromatic/Gin/Lime Juice/Pineapple Juice/Sugar Syrup</p></div>
    <div class="drink" style="top:186px"><div class="drink__top"><span class="drink__name">Candy Rabbit</span><span class="price">$24.00</span></div><p class="drink__desc">Sweet/Fun/Candy Vodka/ Triple sec/Bubblegum Syrup/Sweet and Sour Mix</p></div>
    <div class="drink" style="top:225px"><div class="drink__top"><span class="drink__name">Miss Lulu</span><span class="price">$24.00</span></div><p class="drink__desc">Sweet/Floral/Juicy Gin/Lychee Liqueur/Sweet and Sour Mix/Lychee Juice/raspberry Cordial</p></div>
    <div class="drink" style="top:269px"><div class="drink__top"><span class="drink__name">Merry Carousel</span><span class="price">$24.00</span></div><p class="drink__desc">Citrus/Playful/tart/Gin/Lime Juice/Sugar Syrup</p></div>
    <div class="drink" style="top:310px"><div class="drink__top"><span class="drink__name">Cinnamon Carousel</span><span class="price">$24.00</span></div><p class="drink__desc">cinnamon/Sweet/Rush Firebrand/Vodka/Apple Juice</p></div>
    <div class="drink" style="top:345px"><div class="drink__top"><span class="drink__name">Garden Carafe</span><span class="price">$59.00</span></div><p class="drink__desc">cinnamon/Sweet/Rush Firebrand/Vodka/Apple Juice</p></div>
    <div class="drink" style="top:380px"><div class="drink__top"><span class="drink__name">Party Popper Carafe</span><span class="price">$59.00</span></div><p class="drink__desc">cinnamon/Sweet/Rush Firebrand/Vodka/Apple Juice</p></div>
  </div>

  <div class="extras">
    <div class="section" style="top:27px">
      <span class="band">Beers</span>
      <div class="list">
        <div class="row"><span>harbour lager</span><span class="price">$12.00</span></div>
        <div class="row"><span>far north super crisp</span><span class="price">$12.00</span></div>
        <div class="row"><span>west coast ipa</span><span class="price">$15.00</span></div>
        <div class="row"><span>ember xpa</span><span class="price">$14.00</span></div>
        <div class="row"><span>ginger beer</span><span class="price">$14.00</span></div>
      </div>
    </div>
    <div class="section" style="top:119px">
      <span class="band">Wine on tap</span>
      <div class="list">
        <div class="row"><span>lady fizz pinot grigio</span><span class="price">$12.00</span></div>
        <div class="row"><span>lady fizz rose</span><span class="price">$12.00</span></div>
        <div class="row"><span>clay house sauvignon blanc</span><span class="price">$15.00</span></div>
        <div class="row"><span>stonegate garden of eden</span><span class="price">$14.00</span></div>
      </div>
    </div>
    <div class="section" style="top:202px">
      <span class="band">Shots</span>
      <div class="list">
        <div class="row"><span>cumbre plata tequila</span><span class="price">$12.00</span></div>
        <div class="row"><span>don aurelio</span><span class="price">$12.00</span></div>
        <div class="row"><span>lantern pink</span><span class="price">$15.00</span></div>
        <div class="row"><span>midnight tonic</span><span class="price">$14.00</span></div>
        <div class="row"><span>firebrand cinnamon</span><span class="price">$14.00</span></div>
      </div>
    </div>
  </div>
</section>

</body>
</html>
```